Business Card for Professional Photographer

I'm looking for an eye catching modern clean design that compliments my logo/ website fonts & colours.
I specialise in architecture, corporate & commercial photography so I'm marketing to professional clients rather than portrait / wedding clients.

I would prefer to not have a solid black design.

My logo brand guide is as follows :

Main front font. : Reislust
Main font colour : #fff
Slogan front font : Ubuntu Bold
Monogram front font : Venti Medium
Container colour : #fff

I need print ready files in pdf .png & .eps formats.

Included in the files below are some screen grabs as reference to font & colours etc.

```html
<!DOCTYPE html>
<html lang="en">
<head>
<meta charset="utf-8">
<title>Clearline Frames – Business Card</title>
<link rel="stylesheet" href="https://fonts.googleapis.com/css2?family=Ubuntu:wght@300;400;700&family=Roboto+Condensed:wght@400;700&display=swap">
<style>
  :root {
    --backdrop: #3a3a3c;
    --card-black: #1d1d1f;
    --gold: #c9a24a;
    --gold-light: #ecd48b;
    --gold-dark: #a9822e;
    --ink: #161616;
    --white: #ffffff;
  }
  * { box-sizing: border-box; margin: 0; padding: 0; }
  html, body { width: 799px; height: 1200px; overflow: hidden; }
  body {
    background: var(--backdrop);
    font-family: "Ubuntu", sans-serif;
    position: relative;
  }
  .card {
    position: absolute;
    left: 80px;
    width: 640px;
    height: 360px;
    background: var(--card-black);
    overflow: hidden;
    box-shadow: 0 10px 30px rgba(0,0,0,0.35);
  }
  .card--front { top: 140px; }
  .card--back { top: 700px; }

  /* Front */
  .front-mark {
    position: absolute;
    left: 0; right: 0; top: 95px;
    display: flex; align-items: center; justify-content: center; gap: 16px;
  }
  .front-mark__dot {
    width: 30px; height: 30px; border-radius: 50%;
    border: 4px solid var(--gold);
  }
  .front-mark__name {
    font-family: "Ubuntu", sans-serif;
    font-weight: 300;
    font-size: 38px;
    letter-spacing: 6px;
    text-transform: uppercase;
    color: var(--gold);
  }
  .front-url {
    position: absolute;
    left: 0; right: 0; top: 285px;
    text-align: center;
    font-size: 15px;
    letter-spacing: 3px;
    color: var(--gold);
  }

  /* Back */
  .brand-name {
    position: absolute; left: 40px; top: 26px;
    font-weight: 300; font-size: 30px; letter-spacing: 6px;
    text-transform: uppercase; color: var(--gold);
  }
  .brand-slogan {
    position: absolute; left: 42px; top: 70px;
    font-weight: 700; font-size: 11px; letter-spacing: 3.4px;
    color: var(--white);
  }
  .contact-panel {
    position: absolute; left: 0; top: 110px;
    width: 380px; height: 170px;
    background: linear-gradient(135deg, var(--gold-dark), var(--gold) 45%, var(--gold-light));
    padding: 20px 0 0 50px;
    color: var(--ink);
  }
  .person-name {
    font-family: "Roboto Condensed", sans-serif;
    font-weight: 700; font-size: 22px; line-height: 1;
  }
  .person-role {
    font-family: "Roboto Condensed", sans-serif;
    font-size: 15px; margin-top: 2px; margin-bottom: 10px;
  }
  .contact-list { list-style: none; }
  .contact-list li {
    display: flex; align-items: center; gap: 12px;
    font-family: "Roboto Condensed", sans-serif;
    font-size: 16px; line-height: 25px;
  }
  .contact-list svg { width: 13px; height: 13px; fill: var(--ink); flex: none; }
  .address {
    position: absolute; left: 50px; top: 300px;
    font-family: "Roboto Condensed", sans-serif;
    font-size: 17px; color: var(--white);
  }
  .back-ring {
    position: absolute; left: 420px; top: 150px;
    width: 140px; height: 140px; border-radius: 50%;
    border: 10px solid var(--gold);
  }
  .edge-bar {
    position: absolute; right: 0; top: 175px;
    width: 34px; height: 150px;
    background: linear-gradient(180deg, var(--gold), var(--gold-light));
  }
</style>
</head>
<body>
  <section class="card card--front">
    <div class="front-mark">
      <span class="front-mark__dot"></span>
      <span class="front-mark__name">Clearline Frames</span>
    </div>
    <p class="front-url">www.clearlineframes.com.au</p>
  </section>

  <section class="card card--back">
    <h1 class="brand-name">Clearline Frames</h1>
    <p class="brand-slogan">Architecture Corporate Commercial</p>

    <div class="contact-panel">
      <p class="person-name">Marcus Hale</p>
      <p class="person-role">Photographer</p>
      <ul class="contact-list">
        <li>
          <svg viewBox="0 0 16 16" aria-hidden="true"><path d="M3 1h3l1.5 4-2 1.2a9 9 0 0 0 4.3 4.3L11 8.5l4 1.5v3a2 2 0 0 1-2 2A12 12 0 0 1 1 3a2 2 0 0 1 2-2z"/></svg>
          0400123456
        </li>
        <li>
          <svg viewBox="0 0 16 16" aria-hidden="true"><path d="M1 3h14v10H1z M1.5 3.5 8 9l6.5-5.5" stroke="#ecd48b" stroke-width="1"/></svg>
          info@clearlineframes.com.au
        </li>
        <li>
          <svg viewBox="0 0 16 16" aria-hidden="true"><circle cx="8" cy="8" r="7"/><path d="M1 8h14M8 1c-3 3-3 11 0 14M8 1c3 3 3 11 0 14" stroke="#ecd48b" stroke-width="1" fill="none"/></svg>
          www.clearlineframes.com.au
        </li>
      </ul>
    </div>

    <p class="address">8 Harbour Rd Millbrook Vic 3100</p>
    <span class="back-ring"></span>
    <span class="edge-bar"></span>
  </section>
</body>
</html>
```